Cat-products company needs smart, yet endearing, business card

We need a business card design for a new, but up-and-running, business based in Honolulu, Hawaii. The business is Purrnest Nook Co. Our first product is the most environmentally-friendly cat grass kit ever seen on the planet. Future products, currently in the R&D phase, will include a variety of exciting cat scratchers. We also do consulting work to help apartment-dwellers make their home more cat-friendly and, in the future, plan on doing full, custom installs of structure to create high walkways for cats.

Target Market(s)

Middle-aged, apartment-dwelling, middle-class workers who own 1 or more cats and who dote on them.

Industry/Entity Type

Pet Care

Contact Information for Business Card

A striking, professional, yet warm and friendly design is what we're after.

Font styles to use
Serif
Sans Serif
Other font styles liked:
• Comfortaa

Colors

Designer to choose colors to be used in the design.

Requirements
Must have
• The company logo: (see attachment)
• The company name: Purrnest Nook Co
• The web address: www.purrnestnookco.com
• Email: support@purrnestnookco.com
• Phone: +1 (808) 571 6023
• Update (Fri Jun 30 3017 7:45pm Hawaii Time) I would like, is possible, uploaded picture of the cat grass kit on the back of the card with some text along the lines of: Purrnest Nook Co - Maker Of The Leafiest Feline Sprout Set Yet
Nice to have
• A cat picture, cartoon, real or silhouette that illustrates cats in action and/or relaxing; ie using the apartment space to live, play and relax in and being well-contented.
• Most of the website is done in the font: Comfortaa. It might be nice to continue using this for brand consistency.
Should not have
• Hard-to-read fonts.

```html
<!DOCTYPE html>
<html lang="en">
<head>
<meta charset="utf-8">
<title>Purrnest Nook Co — Business Card</title>
<link href="https://fonts.googleapis.com/css2?family=Comfortaa:wght@400;600;700&display=swap" rel="stylesheet">
<style>
  :root {
    --sun-yellow: #f7b01c;
    --cocoa: #55332c;
    --paper: #ffffff;
    --ink: #3d2a26;
    --backdrop: #e9e6e2;
  }
  * { box-sizing: border-box; margin: 0; padding: 0; }
  html, body {
    width: 1200px;
    height: 1000px;
    overflow: hidden;
    background: var(--backdrop);
    font-family: "Comfortaa", sans-serif;
  }
  .canvas {
    position: relative;
    width: 1200px;
    height: 1000px;
  }
  .card {
    position: absolute;
    left: 250px;
    width: 700px;
    height: 400px;
    overflow: hidden;
    background: var(--paper);
    box-shadow: 0 6px 18px rgba(0,0,0,0.18);
  }
  .card--front { top: 70px; }
  .card--back { top: 530px; }

  .card__shapes {
    position: absolute;
    inset: 0;
    width: 100%;
    height: 100%;
  }

  /* Front */
  .front-name {
    position: absolute;
    left: 0;
    right: 0;
    top: 178px;
    text-align: center;
    font-weight: 700;
    font-size: 40px;
    color: var(--paper);
    letter-spacing: 0.5px;
  }

  /* Back */
  .back-heading {
    position: absolute;
    left: 40px;
    top: 58px;
    font-weight: 700;
    font-size: 34px;
    color: var(--sun-yellow);
  }
  .brand-mark {
    position: absolute;
    right: 40px;
    top: 62px;
    display: flex;
    align-items: center;
    gap: 10px;
  }
  .brand-mark__square {
    width: 26px;
    height: 26px;
    background: var(--sun-yellow);
  }
  .brand-mark__name {
    font-weight: 700;
    font-size: 22px;
    color: var(--cocoa);
  }
  .person {
    position: absolute;
    left: 40px;
    top: 142px;
  }
  .person__name {
    font-weight: 700;
    font-size: 24px;
    color: var(--sun-yellow);
  }
  .person__role {
    font-size: 15px;
    color: var(--ink);
    margin-top: 4px;
  }
  .address {
    position: absolute;
    left: 64px;
    top: 222px;
    font-size: 14px;
    line-height: 20px;
    color: var(--ink);
  }
  .contact-list {
    position: absolute;
    left: 64px;
    top: 276px;
    list-style: none;
    font-size: 14px;
    line-height: 22px;
    color: var(--ink);
  }
  .contact-list li {
    display: flex;
    align-items: center;
    gap: 10px;
  }
  .contact-list svg {
    width: 13px;
    height: 13px;
    fill: var(--sun-yellow);
    flex: none;
  }
  .web-domain { color: var(--sun-yellow); }
</style>
</head>
<body>
<main class="canvas">

  <section class="card card--front" aria-label="Card front">
    <svg class="card__shapes" viewBox="0 0 700 400" preserveAspectRatio="none" aria-hidden="true">
      <rect width="700" height="400" fill="var(--cocoa)"/>
      <polygon points="0,0 640,0 70,400 0,400" fill="var(--sun-yellow)"/>
    </svg>
    <p class="front-name">Purrnest Nook Co</p>
  </section>

  <section class="card card--back" aria-label="Card back">
    <svg class="card__shapes" viewBox="0 0 700 400" preserveAspectRatio="none" aria-hidden="true">
      <polygon points="0,376 548,312 535,400 0,400" fill="var(--sun-yellow)"/>
      <polygon points="560,300 700,284 700,400 546,400" fill="var(--cocoa)"/>
    </svg>

    <h1 class="back-heading">Purrnest Nook Co</h1>

    <div class="brand-mark">
      <span class="brand-mark__square"></span>
      <span class="brand-mark__name">Purrnest Nook Co</span>
    </div>

    <div class="person">
      <p class="person__name">Leilani Akana</p>
      <p class="person__role">Director</p>
    </div>

    <address class="address">
      Your Street Address,<br>
      Country,1234
    </address>

    <ul class="contact-list">
      <li>
        <svg viewBox="0 0 24 24" aria-hidden="true"><path d="M6.6 10.8a15.1 15.1 0 0 0 6.6 6.6l2.2-2.2a1 1 0 0 1 1-.25 11.4 11.4 0 0 0 3.6.57 1 1 0 0 1 1 1V20a1 1 0 0 1-1 1A17 17 0 0 1 3 4a1 1 0 0 1 1-1h3.5a1 1 0 0 1 1 1c0 1.25.2 2.45.57 3.57a1 1 0 0 1-.25 1z"/></svg>
        +1 (808) 571 6023
      </li>
      <li>
        <svg viewBox="0 0 24 24" aria-hidden="true"><path d="M2 5h20v14H2z M2 5l10 8 10-8" stroke="#fff" stroke-width="1.5"/></svg>
        support@purrnestnookco.com
      </li>
      <li>
        <svg viewBox="0 0 24 24" aria-hidden="true"><circle cx="12" cy="12" r="10"/><path d="M2 12h20M12 2c3 3 3 17 0 20M12 2c-3 3-3 17 0 20" stroke="#fff" stroke-width="1.3" fill="none"/></svg>
        <span>www.<span class="web-domain">purrnestnookco</span>.com</span>
      </li>
    </ul>
  </section>

</main>
</body>
</html>
```